Income Tax Business Cards - Updates

Need to update these business cards while keeping all the same wording but just update them and make them look nicer and more modern/ on brand with our brand.

Industry/Entity Type

finance

Contact Information for Business Card

we have multiple locations so will just need to easily be able to change the address and phone numbers

Colors

Designer to choose colors to be used in the design.

```html
<!DOCTYPE html>
<html lang="en">
<head>
<meta charset="utf-8">
<title>Ledgerly Financial Group – Business Cards</title>
<link href="https://fonts.googleapis.com/css2?family=Montserrat:wght@500;600;700;800&display=swap" rel="stylesheet">
<style>
  :root {
    --green: #0f4d2c;
    --red: #c8202a;
    --white: #ffffff;
    --stage: #2b2b2b;
  }
  * { margin: 0; padding: 0; box-sizing: border-box; }
  html, body { width: 1200px; height: 875px; overflow: hidden; }
  body {
    background: var(--stage);
    font-family: "Montserrat", Arial, sans-serif;
    position: relative;
  }
  .card {
    position: absolute;
    left: 320px;
    width: 560px;
    height: 320px;
    border-radius: 26px;
    overflow: hidden;
  }
  .card--front { top: 80px; background: var(--green); color: var(--white); }
  .card--back { top: 475px; background: var(--white); }

  /* front */
  .brand {
    position: absolute;
    left: 0; right: 0;
    display: flex; align-items: center; justify-content: center; gap: 14px;
  }
  .brand__dot { width: 18px; height: 18px; border-radius: 50%; background: var(--red); }
  .brand__name { font-weight: 700; letter-spacing: 0.04em; }
  .card--front .brand { top: 92px; }
  .card--front .brand__name { font-size: 30px; color: var(--white); }
  .card--front .brand__sub {
    position: absolute; top: 136px; left: 0; right: 0; text-align: center;
    font-size: 13px; font-weight: 600; letter-spacing: 0.5em; color: var(--white);
  }
  .front-offer {
    position: absolute; top: 196px; left: 0; right: 0; text-align: center;
    font-weight: 800; text-transform: uppercase; line-height: 1.25;
  }
  .front-offer__lead { font-size: 24px; }
  .front-offer__sub { font-size: 17px; }

  /* back */
  .wave { position: absolute; inset: 0; }
  .back-brand { position: absolute; left: 30px; top: 56px; width: 250px; text-align: center; }
  .back-brand .brand { position: static; gap: 10px; }
  .back-brand .brand__dot { width: 13px; height: 13px; }
  .back-brand .brand__name { font-size: 22px; color: var(--green); }
  .back-brand .brand__sub {
    margin-top: 4px; font-size: 9px; font-weight: 600; letter-spacing: 0.45em; color: var(--green);
  }
  .back-offer {
    position: absolute; left: 30px; top: 122px; width: 250px; text-align: center;
    color: var(--red); font-weight: 800; text-transform: uppercase; line-height: 1.1;
  }
  .back-offer__amount { font-size: 30px; }
  .back-offer__advance { font-size: 18px; margin-top: 2px; }
  .back-offer__note {
    display: flex; align-items: center; gap: 6px; margin: 5px 0;
    color: var(--green); font-size: 9px; font-weight: 700;
  }
  .back-offer__note::before, .back-offer__note::after {
    content: ""; flex: 1; height: 1.5px; background: var(--green);
  }
  .back-offer__free { font-size: 23px; }

  .contact {
    position: absolute; right: 22px; top: 126px; text-align: right; color: var(--white);
  }
  .contact__name { font-size: 22px; font-weight: 800; line-height: 1.2; }
  .contact__title { font-size: 13px; font-weight: 600; margin-bottom: 10px; }
  .contact__line {
    display: flex; align-items: center; justify-content: flex-end; gap: 7px;
    font-size: 11px; font-weight: 500; line-height: 1.75;
  }
  .contact__icon { width: 11px; height: 11px; flex: none; }
</style>
</head>
<body>

  <section class="card card--front">
    <div class="brand">
      <span class="brand__dot"></span>
      <span class="brand__name">LEDGERLY</span>
    </div>
    <div class="brand__sub">FINANCIAL GROUP</div>
    <div class="front-offer">
      <div class="front-offer__lead">File your taxes here</div>
      <div class="front-offer__sub">Up to $6,000 same day advance</div>
    </div>
  </section>

  <section class="card card--back">
    <svg class="wave" viewBox="0 0 560 320" preserveAspectRatio="none" aria-hidden="true">
      <path fill="var(--green)" d="M560 30 C440 34 350 80 335 160 C318 250 240 300 90 320 L560 320 Z"/>
      <path fill="none" stroke="var(--green)" stroke-width="2" d="M520 32 C420 40 338 85 322 160 C305 250 230 298 105 318"/>
      <path fill="var(--red)" d="M510 33 C428 44 362 90 344 152 C360 100 420 58 510 33 Z"/>
    </svg>

    <div class="back-brand">
      <div class="brand">
        <span class="brand__dot"></span>
        <span class="brand__name">LEDGERLY</span>
      </div>
      <div class="brand__sub">FINANCIAL GROUP</div>
    </div>

    <div class="back-offer">
      <div class="back-offer__amount">Up to $6,000</div>
      <div class="back-offer__advance">Same day advance</div>
      <div class="back-offer__note">On approved tax returns!</div>
      <div class="back-offer__free">Free estimates!</div>
    </div>

    <div class="contact">
      <div class="contact__name">Daniel Reyes</div>
      <div class="contact__title">Founder &amp; CEO</div>
      <div class="contact__line">(555) 214-3380
        <svg class="contact__icon" viewBox="0 0 12 12" aria-hidden="true"><path fill="#fff" d="M2.5 1 L4.5 1 L5.2 3.6 L4 4.6 C4.6 6 5.9 7.3 7.4 8 L8.4 6.8 L11 7.5 L11 9.5 C11 10.3 10.3 11 9.5 11 C5 11 1 7 1 2.5 C1 1.7 1.7 1 2.5 1 Z"/></svg>
      </div>
      <div class="contact__line">office@ledgerlyfinancial.com
        <svg class="contact__icon" viewBox="0 0 12 12" aria-hidden="true"><rect x="1" y="2.5" width="10" height="7" fill="#fff"/><path d="M1 2.5 L6 6.5 L11 2.5" fill="none" stroke="var(--green)" stroke-width="1"/></svg>
      </div>
      <div class="contact__line">www.ledgerlyfinancial.com
        <svg class="contact__icon" viewBox="0 0 12 12" aria-hidden="true"><circle cx="6" cy="6" r="5" fill="none" stroke="#fff" stroke-width="1.3"/><path d="M1 6 H11 M6 1 C3.5 4 3.5 8 6 11 M6 1 C8.5 4 8.5 8 6 11" fill="none" stroke="#fff" stroke-width="0.9"/></svg>
      </div>
      <div class="contact__line">Your Address, City, State, Zip 1235
        <svg class="contact__icon" viewBox="0 0 12 12" aria-hidden="true"><path fill="#fff" d="M6 0.5 C3.8 0.5 2.2 2.1 2.2 4.2 C2.2 7 6 11.5 6 11.5 C6 11.5 9.8 7 9.8 4.2 C9.8 2.1 8.2 0.5 6 0.5 Z"/><circle cx="6" cy="4.2" r="1.4" fill="var(--green)"/></svg>
      </div>
    </div>
  </section>

</body>
</html>
```